Falkrin homes and renovations business card design.

Would like some new card designs utilizing my new logo that look professional. I am open to different colors on the logo or utilize the same ones we have. I like the original concept but would like to see some fresh ideas and build on what we have already done.

Target Market(s)

Custom home building industry, Real estate sales, Renovation projects.

Industry/Entity Type

Home Builder

Contact Information for Business Card

Falkrin Homes and Renovations
2871 96th Avenue
Harlow, Westmere
T2R3W8
Home : 403- 718-4063 Cell: 403- 294-5170

My info is : Dax Falkrin, President and CEO
email: falkrinhomes@maildrop-example.net
Website: falkrinhomes-example.com
websit

Requirements
Must have
• Must Use my new logo design. I am open to different colors on the logo or utilize the same ones in the existing design. I can upload the original logo design if needed.

```html
<!DOCTYPE html>
<html lang="en">
<head>
<meta charset="utf-8">
<title>Falkrin Homes and Renovations – Business Card</title>
<link rel="stylesheet" href="https://fonts.googleapis.com/css2?family=Open+Sans:wght@400;600;700;800&display=swap">
<style>
  :root {
    --page-bg: #ecebe8;
    --card-white: #ffffff;
    --card-black: #1d1d1d;
    --card-black-light: #2a2a2a;
    --yellow: #f7b51d;
    --gold: #b88a2c;
    --gold-text: #a97a26;
    --ink: #3c3c3c;
  }
  * { box-sizing: border-box; margin: 0; padding: 0; }
  html, body { width: 1200px; height: 1200px; overflow: hidden; }
  body {
    background: var(--page-bg);
    font-family: "Open Sans", Arial, sans-serif;
    position: relative;
  }
  .card {
    position: absolute;
    left: 120px;
    width: 960px;
    height: 549px;
    overflow: hidden;
    box-shadow: 0 6px 18px rgba(0,0,0,0.15);
  }
  .card--back {
    top: 34px;
    background: linear-gradient(135deg, var(--card-black-light), var(--card-black));
  }
  .card--front {
    top: 617px;
    background: var(--card-white);
  }
  .card__shapes { position: absolute; inset: 0; }

  .wordmark {
    position: absolute;
    display: flex;
    align-items: center;
    gap: 16px;
    font-weight: 800;
    color: var(--gold);
    letter-spacing: 2px;
    line-height: 1;
  }
  .wordmark__square {
    width: 22px; height: 22px;
    background: var(--gold);
  }
  .card--back .wordmark {
    left: 0; right: 0; top: 232px;
    justify-content: center;
    font-size: 84px;
  }
  .card--back .wordmark__square { width: 30px; height: 30px; }
  .card--front .wordmark {
    left: 520px; top: 178px;
    font-size: 64px;
  }

  .owner { position: absolute; left: 96px; top: 40px; }
  .owner__name {
    font-size: 28px; font-weight: 700; color: var(--yellow);
    text-transform: uppercase; letter-spacing: 0.5px;
  }
  .owner__title { font-size: 17px; color: var(--ink); margin-top: 2px; }

  .contacts {
    position: absolute; left: 44px; top: 188px;
    list-style: none;
  }
  .contacts__item {
    display: flex; align-items: center; gap: 12px;
    font-size: 19px; color: var(--gold-text);
    line-height: 30px;
  }
  .contacts__icon { width: 16px; height: 16px; flex: none; }

  .address {
    position: absolute; right: 60px; top: 300px;
    text-align: right; color: var(--gold-text);
    font-size: 21px; line-height: 29px;
    font-style: normal;
  }
  .address__company { font-weight: 700; margin-bottom: 10px; }
</style>
</head>
<body>

<section class="card card--back" aria-label="Card back">
  <div class="wordmark"><span class="wordmark__square"></span>FALKRIN</div>
</section>

<section class="card card--front" aria-label="Card front">
  <svg class="card__shapes" viewBox="0 0 960 549" preserveAspectRatio="none" aria-hidden="true">
    <polygon points="0,0 78,0 78,48 0,48" fill="var(--yellow)"/>
    <polygon points="18,0 58,0 18,40" fill="var(--gold)"/>
    <polygon points="0,338 350,338 370,370 0,370" fill="var(--gold)"/>
    <polygon points="350,338 380,338 420,448 390,448" fill="var(--gold)"/>
    <polygon points="390,448 960,448 960,512 414,512" fill="var(--yellow)"/>
  </svg>

  <div class="owner">
    <h1 class="owner__name">Dax Falkrin</h1>
    <p class="owner__title">President and CEO</p>
  </div>

  <ul class="contacts">
    <li class="contacts__item">
      <svg class="contacts__icon" viewBox="0 0 16 16"><path d="M3 1h3l1.5 4-2 1.2a9 9 0 0 0 4.3 4.3L11 8.5l4 1.5v3a2 2 0 0 1-2 2A13 13 0 0 1 1 3a2 2 0 0 1 2-2z" fill="var(--gold)"/></svg>
      403- 718-4063
    </li>
    <li class="contacts__item">
      <svg class="contacts__icon" viewBox="0 0 16 16"><rect x="4" y="1" width="8" height="14" rx="1.5" fill="none" stroke="var(--gold)" stroke-width="1.6"/><circle cx="8" cy="12.5" r="0.9" fill="var(--gold)"/></svg>
      403- 294-5170
    </li>
    <li class="contacts__item">
      <svg class="contacts__icon" viewBox="0 0 16 16"><rect x="1" y="3" width="14" height="10" rx="1" fill="var(--gold)"/><path d="M1.5 3.5 8 9l6.5-5.5" fill="none" stroke="#fff" stroke-width="1.2"/></svg>
      falkrinhomes@maildrop-example.net
    </li>
    <li class="contacts__item">
      <svg class="contacts__icon" viewBox="0 0 16 16"><circle cx="8" cy="8" r="7" fill="var(--gold)"/><path d="M1 8h14M8 1c-3 3.5-3 10.5 0 14M8 1c3 3.5 3 10.5 0 14" fill="none" stroke="#fff" stroke-width="1"/></svg>
      www.falkrinhomes-example.com
    </li>
  </ul>

  <div class="wordmark"><span class="wordmark__square"></span>FALKRIN</div>

  <address class="address">
    <p class="address__company">Falkrin homes and Renovations</p>
    <p>2871 96th Avenue</p>
    <p>Harlow, Westmere , T2R3W8</p>
  </address>
</section>

</body>
</html>
```